BRAVO Estate Attendant

We require a website built for this company. Logo is also on the attached document. Some info on the company:<br/>To create a work class experience for our clients for property maintenance. A personalised service that deliver’s what landlords need...Quality work, on time and managed from start to finish.<br/>We do things different, our clients deal with one contact, a client manager who manages your maintenance task from start to finish. Our service allows our expert trades people to do what they do best and leave the management/organising to us!<br/>I have drafted up the layout of the web ... very brief at this stage however once we have more info we will add links and can collate more information and provide. <br/>We just want to get a layout of what you think the web should look like and can go from there.

```html
<!DOCTYPE html>
<html lang="en">
<head>
<meta charset="utf-8">
<title>BRAVO Estate Attendant</title>
<link rel="stylesheet" href="https://fonts.googleapis.com/css2?family=Montserrat:wght@300;400;500;600;700&display=swap">
<style>
:root{
  --yellow:#ffc400;
  --dark:#3a3a3a;
  --charcoal:#444446;
  --text:#555;
  --muted:#6b6b6b;
  --light:#f5f5f5;
  --footer-bottom:#1e1e1e;
  --white:#fff;
}
*{margin:0;padding:0;box-sizing:border-box}
html,body{width:1200px;height:3422px;overflow:hidden}
body{font-family:"Montserrat",sans-serif;color:var(--text);background:var(--white);position:relative}

/* header + hero */
.topline{position:absolute;left:0;top:0;width:1200px;height:3px;background:var(--yellow);z-index:3}
.hero{position:absolute;left:0;top:0;width:1200px;height:683px;
  background:linear-gradient(180deg,#6fa6e8 0%,#8db9ee 35%,#c9d4de 62%,#eceae4 80%,#8a7d6c 100%)}
.hero-notch{position:absolute;left:560px;top:660px;width:80px;height:40px}
.brand{position:absolute;left:143px;top:28px;font-size:26px;font-weight:600;color:var(--dark);letter-spacing:.5px;line-height:1}
.brand small{display:block;font-size:12px;margin-top:6px;letter-spacing:1px}
.nav{position:absolute;left:409px;top:50px;display:flex;gap:37px;font-size:14px;font-weight:600;color:#1e1e1e}
.nav .active{position:relative}
.nav .active::after{content:"";position:absolute;left:0;right:0;top:26px;height:2px;background:var(--yellow)}
.search{position:absolute;left:1020px;top:41px;width:34px;height:34px;border-radius:50%;background:var(--yellow)}
.hero-title{position:absolute;left:0;top:237px;width:1200px;text-align:center}
.hero-title span{display:inline-block;height:100px;padding:0 16px;background:var(--yellow);
  font-size:88px;font-weight:500;color:var(--dark);line-height:100px;letter-spacing:-1px}
.hero-sub{position:absolute;left:0;width:1200px;top:360px;text-align:center;font-size:44px;font-weight:700;color:var(--white);letter-spacing:1px}
.play{position:absolute;left:571px;top:446px;width:58px;height:58px}

/* section titles */
.section-title{position:absolute;left:0;width:1200px;text-align:center;font-size:38px;font-weight:700;color:var(--dark);letter-spacing:1px;z-index:2}
.section-title span{color:var(--yellow)}
.lead{position:absolute;left:190px;width:820px;text-align:center;font-size:13.5px;font-weight:300;line-height:32px;color:var(--muted)}

/* services grid */
.services{position:absolute;left:143px;top:953px;width:915px;height:494px;display:grid;grid-template-columns:repeat(3,305px);grid-template-rows:repeat(2,247px)}
.tile{padding:8px 8px 0;display:flex;flex-direction:column}
.tile.yellow{background:var(--yellow);color:var(--dark)}
.tile.grey{background:var(--charcoal);color:var(--white)}
.tile-photo{height:164px}
.tile-label{flex:1;display:flex;align-items:center;justify-content:center;text-align:center;font-size:19.5px;font-weight:700;letter-spacing:.5px;line-height:24px}

/* about */
.about-photo{position:absolute;left:0;top:1557px;width:600px;height:498px;background:linear-gradient(135deg,#9a7f6a 0%,#c9c3bb 40%,#3a4a8a 75%,#2b3670 100%)}
.about-card{position:absolute;left:537px;top:1622px;width:519px;height:368px;background:var(--white);box-shadow:0 0 22px rgba(255,196,0,.14);text-align:center}
.about-card h2{font-size:38px;font-weight:700;color:var(--dark);margin-top:52px;letter-spacing:1px}
.about-card h2 span{color:var(--yellow)}
.about-card p{font-size:13.5px;font-weight:300;line-height:29px;color:var(--muted);width:410px;margin:18px auto 0}
.btn{display:inline-flex;align-items:center;justify-content:center;gap:8px;background:var(--yellow);color:var(--white);font-weight:700;border-radius:30px;letter-spacing:.5px}
.about-card .btn{width:172px;height:46px;font-size:14.5px;margin-top:29px}

/* benefits */
.benefits{position:absolute;left:0;top:2055px;width:1200px;height:496px;background:linear-gradient(160deg,#fafafa,#f3f3f3 60%,#fbfbfb)}
.benefit{position:absolute;top:2274px;width:190px;text-align:center}
.benefit svg{display:block;margin:0 auto}
.benefit h3{font-size:13.5px;font-weight:600;color:var(--dark);margin-top:22px;letter-spacing:.3px}
.benefit p{font-size:13px;font-weight:300;color:var(--muted);line-height:21px;margin-top:8px}
.arrow{position:absolute;top:2337px}

/* contact */
.contact{position:absolute;left:0;top:2551px;width:1200px;height:564px;background:var(--light)}
.field{position:absolute;height:41px;border:1.5px solid #555;border-radius:22px;background:var(--white);font-size:12px;color:#555;padding-left:29px;line-height:38px;z-index:2}
.field.message{height:73px;border-radius:26px;line-height:1;padding-top:14px}
.submit{position:absolute;left:487px;top:2966px;width:227px;height:48px;font-size:15px;z-index:2}

/* footer */
.footer{position:absolute;left:0;top:3115px;width:1200px;height:247px;background:linear-gradient(180deg,#3a3a3a,#262626)}
.footer-notch{position:absolute;left:560px;top:3109px;width:80px;height:30px}
.footer-brand{position:absolute;left:146px;top:3178px;font-size:52px;font-weight:600;color:var(--white);line-height:1;letter-spacing:-.5px}
.footer-brand small{display:block;font-size:15px;margin-top:6px;letter-spacing:.5px}
.socials{position:absolute;left:146px;top:3280px;display:flex;gap:4px}
.socials span{width:30px;height:30px;border:1.5px solid var(--white);border-radius:50%}
.fcol{position:absolute;top:3178px;color:var(--white)}
.fcol h4{font-size:17px;font-weight:600;letter-spacing:.3px;margin-bottom:8px}
.fcol p{font-size:12.5px;font-weight:400;line-height:30px}
.bottom{position:absolute;left:0;top:3362px;width:1200px;height:60px;background:var(--footer-bottom);color:#ddd;font-size:11.5px;text-align:center;line-height:60px}
</style>
</head>
<body>

<div class="hero" role="img" aria-label="Modern two-storey luxury home at dusk with lit windows and blue sky"></div>
<div class="topline"></div>
<div class="brand">BRAVO<small>ESTATE ATTENDANT</small></div>
<nav class="nav">
  <span class="active">HOME</span><span>ABOUT US</span><span>SERVICES</span><span>BENEFITS</span><span>NEWS</span><span>CONTACT</span>
</nav>
<div class="search">
  <svg width="34" height="34" viewBox="0 0 34 34"><circle cx="16" cy="16" r="4.5" fill="none" stroke="#222" stroke-width="2"/><line x1="19.2" y1="19.2" x2="22" y2="22" stroke="#222" stroke-width="2.4" stroke-linecap="round"/></svg>
</div>
<div class="hero-title"><span>BRAVO</span></div>
<div class="hero-sub">ESTATE ATTENDANT</div>
<svg class="play" viewBox="0 0 58 58"><circle cx="29" cy="29" r="26" fill="none" stroke="#fff" stroke-width="3.5"/><path d="M23 18 L40 29 L23 40 Z" fill="#fff"/></svg>
<svg class="hero-notch" viewBox="0 0 80 40"><path d="M0 23 Q20 23 40 3 Q60 23 80 23 L80 40 L0 40 Z" fill="#fff"/><path d="M33 14 L40 20 L47 14" fill="none" stroke="#999" stroke-width="1.3"/></svg>

<h2 class="section-title" style="top:768px">WHAT <span>WE DO</span></h2>
<p class="lead" style="top:838px">Lorem ipsum dolor sit amet, consectetur adipiscing elit, sed do eiusmod tempor incididunt ut labore et dolore magna aliqua. Ut enim ad minim veniam, quis nostrud exercitation ulisi ut aliquip ex ea commodo consequat.</p>

<section class="services">
  <div class="tile yellow"><div class="tile-photo" role="img" aria-label="Tradesman on the phone at a laptop" style="background:linear-gradient(135deg,#c8d3dc,#5b82b4 55%,#dfe3e6)"></div><div class="tile-label">TRADE PEOPLE</div></div>
  <div class="tile grey"><div class="tile-photo" role="img" aria-label="Campervan parked on a grassy coast" style="background:linear-gradient(180deg,#5f98d2 0%,#a9c7e3 45%,#b58a4f 70%,#8a6a38 100%)"></div><div class="tile-label">REMOVALIST VAN<br>AND TRAILERS</div></div>
  <div class="tile yellow"><div class="tile-photo" role="img" aria-label="Coins and financial charts" style="background:linear-gradient(135deg,#3a3f8a,#b03a5a 50%,#e07a58 70%,#3b6fa8)"></div><div class="tile-label">CONNECTIONS</div></div>
  <div class="tile grey"><div class="tile-photo" role="img" aria-label="Ceiling smoke alarm with smoke" style="background:linear-gradient(135deg,#e8e8ea,#d9c8cc 50%,#f2f2f2)"></div><div class="tile-label">SMOKE ALARMS</div></div>
  <div class="tile yellow"><div class="tile-photo" role="img" aria-label="Business people reviewing financial documents" style="background:linear-gradient(135deg,#2a3a55,#8ba6c4 50%,#dce4ec)"></div><div class="tile-label">FINANCE</div></div>
  <div class="tile grey"><div class="tile-photo" role="img" aria-label="Family silhouettes at sunset" style="background:linear-gradient(180deg,#7d7a72,#c9b48a 55%,#1e1e1e 100%)"></div><div class="tile-label">WEALTH CREATION</div></div>
</section>

<div class="about-photo" role="img" aria-label="Two estate agents in suits holding a folder and plans outside a building"></div>
<div class="about-card">
  <h2>ABOUT <span>US</span></h2>
  <p>Lorem ipsum dolor sit amet, consectetur adipiscing elit, sed do eiusmod tempor incididunt ut labore et dolore magna aliqua. Ut enim ad minim veniam, quis nostrud exercitation ulisi ut aliquip ex ea commodo consequat.</p>
  <span class="btn">READ MORE
    <svg width="14" height="14" viewBox="0 0 14 14"><circle cx="7" cy="7" r="7" fill="#fff"/><path d="M5.5 4 L8.5 7 L5.5 10" fill="none" stroke="#ffc400" stroke-width="2"/></svg></span>
</div>

<div class="benefits"></div>
<h2 class="section-title" style="top:2170px">OUR <span>BENEFITS</span></h2>
<svg class="arrow" style="left:63px" width="34" height="64" viewBox="0 0 34 64"><path d="M32 1 L2 32 L32 63" fill="none" stroke="#9a9a9a" stroke-width="1.3"/></svg>
<svg class="arrow" style="left:1103px" width="34" height="64" viewBox="0 0 34 64"><path d="M2 1 L32 32 L2 63" fill="none" stroke="#9a9a9a" stroke-width="1.3"/></svg>

<div class="benefit" style="left:136px">
  <svg width="94" height="94" viewBox="0 0 94 94"><circle cx="47" cy="47" r="45" fill="none" stroke="#ffc400" stroke-width="3"/><circle cx="47" cy="47" r="37" fill="#fff" stroke="#444" stroke-width="2"/><path d="M33 52 V46 A14 14 0 0 1 61 46 V52" fill="none" stroke="#ffc400" stroke-width="4"/><rect x="30" y="47" width="8" height="12" rx="3" fill="#ffc400"/><rect x="56" y="47" width="8" height="12" rx="3" fill="#ffc400"/></svg>
  <h3>CUSTOMER SERVICE</h3><p>Lorem ipsum dolor sit amet, sed dousmod tempor</p>
</div>
<div class="benefit" style="left:382px">
  <svg width="94" height="94" viewBox="0 0 94 94"><circle cx="47" cy="47" r="45" fill="none" stroke="#ffc400" stroke-width="3"/><circle cx="47" cy="47" r="37" fill="#fff" stroke="#444" stroke-width="2"/><path d="M33 52 V46 A14 14 0 0 1 61 46 V52" fill="none" stroke="#ffc400" stroke-width="4"/><rect x="30" y="47" width="8" height="12" rx="3" fill="#ffc400"/><rect x="56" y="47" width="8" height="12" rx="3" fill="#ffc400"/></svg>
  <h3>CALL CENTRE</h3><p>Lorem ipsum dolor sit amet, sed dousmod tempor</p>
</div>
<div class="benefit" style="left:627px">
  <svg width="94" height="94" viewBox="0 0 94 94"><circle cx="47" cy="47" r="45" fill="none" stroke="#ffc400" stroke-width="3"/><circle cx="47" cy="47" r="37" fill="#fff" stroke="#444" stroke-width="2"/><rect x="32" y="45" width="7" height="16" rx="1.5" fill="#ffc400"/><path d="M41 45 L48 33 Q52 31 52 36 L50 43 H59 Q63 44 61 48 L58 59 Q57 61 54 61 H41 Z" fill="#ffc400"/></svg>
  <h3>VALUES</h3><p>Lorem ipsum dolor sit amet, sed dousmod tempor</p>
</div>
<div class="benefit" style="left:872px">
  <svg width="94" height="94" viewBox="0 0 94 94"><circle cx="47" cy="47" r="45" fill="none" stroke="#ffc400" stroke-width="3"/><circle cx="47" cy="47" r="37" fill="#fff" stroke="#444" stroke-width="2"/><path d="M30 34 V44 L48 62 L60 50 L42 32 H32 Z" fill="#ffc400"/><circle cx="36.5" cy="38.5" r="2.6" fill="#fff"/><path d="M45 32 L63 50" stroke="#ffc400" stroke-width="3"/></svg>
  <h3>PRICING</h3><p>Lorem ipsum dolor sit amet, sed dousmod tempor</p>
</div>

<section class="contact"></section>
<h2 class="section-title" style="top:2644px">CONTACT <span>FORM</span></h2>
<div class="field" style="left:219px;top:2740px;width:371px">Enter Name</div>
<div class="field" style="left:610px;top:2740px;width:371px">Enter Email</div>
<div class="field" style="left:219px;top:2800px;width:371px">Phone</div>
<div class="field" style="left:610px;top:2800px;width:371px">Address</div>
<div class="field message" style="left:219px;top:2860px;width:762px">Message</div>
<span class="btn submit">SUBMIT MESSAGE
  <svg width="14" height="14" viewBox="0 0 14 14"><circle cx="7" cy="7" r="7" fill="#fff"/><path d="M5.5 4 L8.5 7 L5.5 10" fill="none" stroke="#ffc400" stroke-width="2"/></svg></span>

<footer class="footer"></footer>
<svg class="footer-notch" viewBox="0 0 80 30"><path d="M0 6 Q20 6 40 26 Q60 6 80 6 L80 0 L0 0 Z" fill="#f5f5f5"/><path d="M34 16 L40 11 L46 16" fill="none" stroke="#bbb" stroke-width="1.3"/></svg>
<div class="footer-brand">BRAVO<small>ESTATE ATTENDANT</small></div>
<div class="socials"><span></span><span></span><span></span><span></span></div>
<div class="fcol" style="left:405px"><h4>CONTACT US</h4><p>Phone : 1 555 010 2020<br>Email : info@bravoestateattendant.com</p></div>
<div class="fcol" style="left:735px"><h4>ABOUT US</h4><p>Team<br>Concept<br>Location</p></div>
<div class="fcol" style="left:894px"><h4>OPENING HOURS</h4><p>Monday - Saturday<br>7:00am to 5:00pm</p></div>
<div class="bottom">© 2019 BRAVO Estate Attendant. All right reserved &nbsp;Term of Use &nbsp;| &nbsp;Privacy policy</div>

</body>
</html>
```